Brovo like IOS/Android app for Okinawa Island - TaruSeeker

TaruSeeker is the name of the app
The closest thing that I can relate this app to is a region specific Brovo app. The app is for the island of Okinawa and is geared towards English speaking travelers. The style of app that I prefer is a look and feel similar to that of the new Nestory app, color should also be similar if not the same as the nestory app.

The app needs to have the following screens

LOGIN SCREEN
1. App login page with a login for chatterly button or create an account option. Personally I would like an image in the background with a real beachy feel, but don't do this if it messes with your design.

2. Depending on the choice of login there will need to be a second login screen to create the account. Nestory does this nicely.

PRIMARY HOME
primary page similar to the primary layout when you get into the nestory app.
This page is kind of like the home page of the app and should include the following items:
search field
upcoming events
popular things to do
featured restaurants
Featured Places to stay
area guides
Moving here
(this will allow the person to select, housing agencies, auto dealers, schools etc) These are essentially just quick searches.
Each selection should be listed so that the user can swipe to the left or right in order to view more listings under the categories listed above. It will not be the full list but rather a sample.

SIDEBAR POPOUT MENU
Popout sidebar that contains the following selections
Places to Eat
Things to do
Attractions
Beaches
Shop
Farmers Markets
Places to Stay
Schools & DayCare
Housing
Auto
Events
Account settings
Add a business

LIST VIEW
4. List view page for whatever category the user selected. This will show all the listings for the specific category: The top should also have the featured listings for that category

INDIVIDUAL LISTING
5. Listing page
This will include photos, description, hours, map(this can be a button to view the map or the map), Reviews with a leave a review option

AREA GUIDES
6. Area Guides. This is where the user will be able to select a specific area and learn about it. It should include an area where there can be a description, photos with a hero photo image, a map, popular local attractions or things to do, best restaurants in the area, places to stay etc.

PROFILE PAGE
7. Profile page for the user where they can make any updates they need to

Every page but the listing page should include the search bar. When the user clicks in it they should be able to see a drop down of quick select searches or run a regular search.

Logo
I have attached a logo that was made that needs a redesign. The map marker contains the logo for Okinawa within it so it does need to be similar.

If you have any questions or need clarification please send me a message. I will respond promptly.
Thank you,

Industry/Entity Type

Android

Logo Text

TaruSeeker

```html
<!DOCTYPE html>
<html lang="en">
<head>
<meta charset="utf-8">
<title>TaruSeeker – Sidebar Menu</title>
<link href="https://fonts.googleapis.com/css2?family=Figtree:wght@400;500;700&display=swap" rel="stylesheet">
<style>
  :root {
    --coral: #e85a6a;
    --ink: #1f1f24;
    --muted: #9a9aa0;
    --page: #f1f1f1;
    --panel: #ffffff;
    --strip: #f7f7f7;
    --rule: #e6e6e6;
  }
  * { box-sizing: border-box; margin: 0; padding: 0; }
  html, body {
    width: 1200px; height: 1200px; overflow: hidden;
    background: var(--page);
    font-family: "Figtree", sans-serif;
  }
  .device {
    position: absolute; left: 300px; top: 66px;
    width: 600px; height: 1068px;
    background: var(--strip);
    box-shadow: 0 10px 60px rgba(0,0,0,0.12);
    overflow: hidden;
  }
  /* Sidebar */
  .sidebar {
    position: absolute; left: 0; top: 0; width: 480px; height: 100%;
    background: var(--panel);
    box-shadow: 2px 0 10px rgba(0,0,0,0.05);
    z-index: 2;
  }
  .sidebar-header {
    position: relative; height: 100px;
    border-bottom: 3px solid var(--coral);
  }
  .brand {
    position: absolute; left: 24px; top: 26px;
    display: flex; align-items: center; gap: 10px;
  }
  .brand-dot {
    width: 52px; height: 52px; border-radius: 50%;
    background: var(--coral);
  }
  .brand-name {
    font-size: 28px; font-weight: 500; color: var(--coral); letter-spacing: 0.2px;
  }
  .header-divider {
    position: absolute; left: 318px; top: 38px; width: 1px; height: 33px;
    background: var(--rule);
  }
  .settings {
    position: absolute; left: 336px; top: 41px;
    display: flex; align-items: center; gap: 8px;
    color: var(--coral); font-size: 22px;
  }
  .menu { list-style: none; position: absolute; left: 0; top: 123px; width: 100%; }
  .menu-item {
    height: 78.4px; display: flex; align-items: center;
    padding-left: 34px;
  }
  .menu-item svg { width: 40px; height: 40px; flex: none; }
  .menu-label {
    margin-left: 21px; font-size: 23px; font-weight: 400;
    letter-spacing: 1.6px; color: var(--ink);
  }
  .icon { fill: none; stroke: var(--coral); stroke-width: 1.6; stroke-linecap: round; stroke-linejoin: round; }

  /* Home screen peeking behind */
  .home { position: absolute; left: 480px; top: 0; width: 120px; height: 100%; overflow: hidden; }
  .topbar { height: 102px; border-bottom: 1px solid var(--rule); position: relative; }
  .hamburger { position: absolute; left: 27px; top: 60px; width: 28px; }
  .hamburger span { display: block; height: 2px; background: var(--coral); margin-bottom: 8px; }
  .search {
    position: relative; height: 72px; background: var(--panel);
    border-bottom: 1px solid var(--rule);
    white-space: nowrap;
  }
  .search svg { position: absolute; left: 28px; top: 25px; }
  .search-text { position: absolute; left: 64px; top: 23px; font-size: 22px; color: var(--muted); letter-spacing: 0.5px; }
  .section-title {
    position: absolute; left: 28px; white-space: nowrap;
    font-size: 38px; line-height: 1; font-weight: 700; color: var(--coral);
  }
  .section-upcoming { top: 208px; }
  .section-popular { top: 552px; }
  .section-featured { top: 896px; }
  .sub-title {
    position: absolute; left: 28px; top: 964px; white-space: nowrap;
    font-size: 24px; line-height: 1; font-weight: 700; color: var(--ink);
  }
  .card { position: absolute; left: 29px; width: 240px; border-radius: 5px; }
  .card-event { top: 275px; height: 224px; background: linear-gradient(180deg, #3f5f88 0%, #a5464e 45%, #2a2a2a 100%); }
  .card-popular { top: 619px; height: 224px; background: linear-gradient(160deg, #c9b92a 0%, #8b8520 50%, #1e1e1a 100%); }
  .card-restaurant { top: 1004px; height: 120px; background: linear-gradient(180deg, #d9dbd6 0%, #5b6455 60%, #2d3128 100%); }
</style>
</head>
<body>
<div class="device">
  <aside class="sidebar">
    <header class="sidebar-header">
      <div class="brand">
        <div class="brand-dot"></div>
        <span class="brand-name">TaruSeeker</span>
      </div>
      <div class="header-divider"></div>
      <div class="settings">
        <svg width="22" height="22" viewBox="0 0 24 24" class="icon"><circle cx="12" cy="12" r="3.2"/><path d="M12 2.5l1.6 2.6 3-.8.8 3 2.6 1.6-1.4 2.7 1.4 2.7-2.6 1.6-.8 3-3-.8L12 21.5l-1.6-2.6-3 .8-.8-3L4 15.1l1.4-2.7L4 9.7l2.6-1.6.8-3 3 .8z"/></svg>
        <span>Settings</span>
      </div>
    </header>

    <ul class="menu">
      <li class="menu-item">
        <svg viewBox="0 0 48 48" class="icon"><path d="M4 3h12l-1 10a5 5 0 0 1-10 0z M10 18v26 M5 44h10"/><path d="M24 3v12a3 3 0 0 0 6 0V3 M27 3v41 M38 3c4 3 4 14 0 18v23 M38 3v41"/></svg>
        <span class="menu-label">PLACES TO EAT</span>
      </li>
      <li class="menu-item">
        <svg viewBox="0 0 48 48" class="icon"><circle cx="18" cy="20" r="15"/><circle cx="18" cy="20" r="9"/><circle cx="18" cy="20" r="3"/><path d="M18 20L44 20 M40 16l4 4-4 4 M36 16l4 4-4 4 M10 34l-2 10 M26 34l2 10"/></svg>
        <span class="menu-label">THINGS TO DO</span>
      </li>
      <li class="menu-item">
        <svg viewBox="0 0 48 48" class="icon"><path d="M24 38s-11-13-11-22a11 11 0 0 1 22 0c0 9-11 22-11 22z"/><circle cx="24" cy="15" r="4"/><path d="M16 34H9L4 45h40l-5-11h-7"/></svg>
        <span class="menu-label">ATTRACTIONS</span>
      </li>
      <li class="menu-item">
        <svg viewBox="0 0 48 48" class="icon"><path d="M10 16C14 4 34 0 46 8c-6-2-10 0-12 4-4-3-10-2-12 2-4-3-10-2-12 2z M28 12l10 34 M4 34l26 12 M6 26l8 16 M18 30l-8 12"/></svg>
        <span class="menu-label">BEACHES</span>
      </li>
      <li class="menu-item">
        <svg viewBox="0 0 48 48" class="icon"><path d="M2 4h6l4 28h30 M8 12h38l-4 14H11"/><circle cx="16" cy="40" r="3"/><circle cx="38" cy="40" r="3"/></svg>
        <span class="menu-label">SHOP</span>
      </li>
      <li class="menu-item">
        <svg viewBox="0 0 48 48" class="icon"><path d="M3 46V10l3-4 3 4v36 M19 46V10l3-4 3 4v36 M35 46V10l3-4 3 4v36 M9 18h10 M9 34h10 M25 18h10 M25 34h10 M41 18h4 M41 34h4 M13 8v38 M29 8v38 M45 8v38"/></svg>
        <span class="menu-label">FARMERS MARKETS</span>
      </li>
      <li class="menu-item">
        <svg viewBox="0 0 48 48" class="icon"><path d="M6 24V6h36v18 M2 24h44v16H2z M2 32h44 M4 40v4 M44 40v4 M12 24v-8h10v8 M26 24v-8h10v8"/></svg>
        <span class="menu-label">PLACES TO STAY</span>
      </li>
      <li class="menu-item">
        <svg viewBox="0 0 48 48" class="icon"><path d="M2 14h44l-6 10H8z M10 24v14c8 4 20 4 28 0V24 M6 20v16 M4 36h4v4H4z"/></svg>
        <span class="menu-label">SCHOOLS &amp; DAYCARE</span>
      </li>
      <li class="menu-item">
        <svg viewBox="0 0 48 48" class="icon"><path d="M2 24L24 3l22 21 M7 19v27h34V19 M18 46V32h12v14"/></svg>
        <span class="menu-label">HOUSING</span>
      </li>
      <li class="menu-item">
        <svg viewBox="0 0 48 48" class="icon"><path d="M10 18l4-10h20l4 10 M4 18h40v20H4z M6 38v6h6v-6 M36 38v6h6v-6 M2 16h6 M40 16h6 M18 28h12 M18 32h12 M20 8V4h8v4"/><circle cx="11" cy="28" r="3"/><circle cx="37" cy="28" r="3"/></svg>
        <span class="menu-label">AUTO</span>
      </li>
      <li class="menu-item">
        <svg viewBox="0 0 48 48" class="icon"><rect x="3" y="4" width="42" height="42" rx="3"/><path d="M3 13h42 M13 4v4 M35 4v4"/><text x="24" y="40" text-anchor="middle" font-family="Figtree, sans-serif" font-size="20" fill="none" stroke="#e85a6a" stroke-width="1">31</text></svg>
        <span class="menu-label">EVENTS</span>
      </li>
      <li class="menu-item">
        <svg viewBox="0 0 48 48" class="icon"><rect x="3" y="12" width="42" height="32" rx="3"/><path d="M17 12V6h14v6 M3 22h42"/></svg>
        <span class="menu-label">ADD A BUSINESS</span>
      </li>
    </ul>
  </aside>

  <main class="home">
    <div class="topbar">
      <div class="hamburger"><span></span><span></span><span></span></div>
    </div>
    <div class="search">
      <svg width="24" height="24" viewBox="0 0 24 24" fill="none" stroke="#9a9aa0" stroke-width="1.6"><circle cx="10" cy="10" r="8"/><path d="M16 16l6 6"/></svg>
      <span class="search-text">Search TaruSeeker</span>
    </div>
    <h2 class="section-title section-upcoming">Upcoming Events</h2>
    <div class="card card-event" role="img" aria-label="Photo of a festival drummer performing at an Eisa event"></div>
    <h2 class="section-title section-popular">Popular Things to Do</h2>
    <div class="card card-popular" role="img" aria-label="Photo of a popular outdoor activity at golden hour"></div>
    <h2 class="section-title section-featured">Featured</h2>
    <h3 class="sub-title">Restaurants</h3>
    <div class="card card-restaurant" role="img" aria-label="Photo of a Japanese set meal with rice bowls and grilled fish"></div>
  </main>
</div>
</body>
</html>
```